Open Harbor book needs a cover design

I need a front and back cover design that demonstrates a strong sense of possibility that trust can be repaired even if things look bleak. Repairing trust is difficult, but this book is full of wisdom, proven strategies, and doctoral research to help people strengthen relationships and improve trust. It can help any group: business, nonprofit, education, service. Showing diversity of groups and people is very important. For the cover title, there should be a play on words: "Open Harbor: Is it? Within Reach" should have the words "is it?" crossed out and the words "It IS! should be replaced there in a striking way. Perhaps in red ink. For publishing purposes, book will be titled Open Harbor: It IS Within Reach! Please see the attachment for an example. The book layout is approximately 260 pages.

A business self-help book, but the target is any person in a group that feels they have lost trust in each other. It can be just a normal person struggling in a volunteer group they are a part of, or a supervisor whose group is not working well together. It can be a leader who just wants their group to be stronger.

Business Management

• Allise - I believe is being used on the interior of the book for the title page and headings

• Show hope and possibility in the midst of difficulty. Must have a play on the words in the title "Open Harbor: Is it? Within Reach" with crossing out "is it?" with "It IS!" (see attached example) Must include the author's name: Marla Quentin, PhD Must include a smaller tagline: "Practical Steps to Move Teams Forward Again"
• Showing diverse people, or hands. Diverse kinds of groups - not just business. A colorful cover. Maybe show the complexity of trust when it is broken...broken pieces of trust that are then picked up and put together when people work together. Could show people (or images of hands) or other ways to show that it's a choice and it is possible to repair broken trust. I'd also like to convey a sense of a group - not just random people. That they have something at stake to work on repairing trust together and this book can help them.
• If images of people are used, just showing one gender or race is not okay. Nor just binary choices: like an image containing one man and one woman, or one white person and one person of color - otherwise it seems that the book on Open Harbor is about race or gender relations.

```html
<!DOCTYPE html>
<html lang="en">
<head>
<meta charset="utf-8">
<title>Open Harbor – Book Cover</title>
<link rel="stylesheet" href="https://fonts.googleapis.com/css2?family=Overlock:wght@400;700&family=Pompiere&family=Libre+Baskerville&display=swap">
<style>
  :root {
    --backdrop-edge: #cfe6f4;
    --backdrop-centre: #e6f3fb;
    --cover-white: #ffffff;
    --ink-dark: #3f3b3c;
    --ink-author: #222022;
    --ink-red: #e5121c;
    --cradle-silver: #eef0f3;
    --cradle-mist: #f6f4f5;
    --cradle-red: #f3d6d8;
  }
  html, body {
    margin: 0;
    width: 1200px;
    height: 1200px;
    overflow: hidden;
  }
  body {
    position: relative;
    background: radial-gradient(circle at 50% 50%, var(--backdrop-centre) 0%, var(--backdrop-edge) 75%);
  }
  .book-cover {
    position: absolute;
    left: 232px;
    top: 48px;
    width: 736px;
    height: 1104px;
    background: var(--cover-white);
    overflow: hidden;
  }
  .cradle-art {
    position: absolute;
    left: 60px;
    top: 0;
    width: 630px;
    height: 320px;
    background: linear-gradient(90deg, var(--cradle-silver) 0%, var(--cradle-mist) 65%, var(--cradle-red) 100%);
  }
  .title-open,
  .title-harbor,
  .title-struck,
  .title-answer,
  .title-reach,
  .tagline,
  .author {
    position: absolute;
    margin: 0;
    white-space: nowrap;
    line-height: 1;
  }
  .title-open {
    left: 266px;
    top: 362px;
    font-family: "Overlock", sans-serif;
    font-weight: 400;
    font-size: 160px;
    letter-spacing: -2px;
    color: var(--ink-dark);
    transform: scaleX(0.85);
    transform-origin: left top;
  }
  .title-harbor {
    left: 138px;
    top: 462px;
    font-family: "Overlock", sans-serif;
    font-weight: 400;
    font-size: 222px;
    letter-spacing: -6px;
    color: var(--ink-red);
    transform: scaleX(0.8);
    transform-origin: left top;
  }
  .title-struck {
    left: 368px;
    top: 712px;
    font-family: "Pompiere", sans-serif;
    font-size: 60px;
    color: var(--ink-dark);
  }
  .title-struck::after {
    content: "";
    position: absolute;
    left: -4px;
    right: -4px;
    top: 54%;
    height: 4px;
    background: var(--ink-red);
  }
  .title-answer {
    left: 490px;
    top: 704px;
    font-family: "Pompiere", sans-serif;
    font-size: 64px;
    color: var(--ink-red);
  }
  .title-reach {
    left: 0;
    width: 736px;
    text-align: center;
    top: 772px;
    font-family: "Pompiere", sans-serif;
    font-size: 74px;
    color: var(--ink-dark);
  }
  .tagline {
    left: 0;
    width: 712px;
    text-align: center;
    top: 880px;
    font-family: "Pompiere", sans-serif;
    font-size: 32px;
    line-height: 34px;
    color: var(--ink-dark);
  }
  .author {
    left: 0;
    width: 732px;
    text-align: center;
    top: 1008px;
    font-family: "Libre Baskerville", serif;
    font-size: 36px;
    color: var(--ink-author);
  }
</style>
</head>
<body>
  <main class="book-cover">
    <div class="cradle-art" role="img" aria-label="Newton's cradle: four silver balls hanging still while one red ball swings out to the right"></div>
    <h1 class="title-open">Open</h1>
    <p class="title-harbor">Harbor</p>
    <p class="title-struck">Is it?</p>
    <p class="title-answer">It IS!</p>
    <p class="title-reach">Within Reach</p>
    <p class="tagline">Practical Steps<br>to Move Teams Forward Again</p>
    <p class="author">Marla Quentin, PhD</p>
  </main>
</body>
</html>
```